QVR business card

Need a business card for a company that provides instructional design and elearning development services. The website is here: http://quorvane.studio/

I'm attaching a current logo, as well as the old business card design. While I like to keep it clean, the old design is too simplistic for my liking. The only idea I want to reuse from the old design is placing industry jargon on the back of the card, just need a better way to present it. But if you have other ideas for the back--feel free to experiment.

Please use the colors complementary to the color we have on the website. Thank you!

```html
<!DOCTYPE html>
<html lang="en">
<head>
<meta charset="utf-8">
<title>QVR business card</title>
<link rel="stylesheet" href="https://fonts.googleapis.com/css2?family=Montserrat:wght@600;700&family=Roboto+Condensed:wght@700&family=Roboto:wght@400&display=swap">
<style>
  :root {
    --backdrop: #a8a6a6;
    --card-dark: #2e2f33;
    --card-light: #f4f4f3;
    --teal: #1fb39a;
    --teal-deep: #38b2a4;
    --teal-mint: #a6d38c;
    --gold: #d6cd86;
    --ink: #2f2f33;
    --white: #ffffff;
  }
  * { margin: 0; padding: 0; box-sizing: border-box; }
  html, body {
    width: 1200px; height: 1200px; overflow: hidden;
    background: var(--backdrop);
  }
  .canvas { position: relative; width: 1200px; height: 1200px; }

  .card {
    position: absolute;
    border-radius: 22px;
    overflow: hidden;
  }
  .card-back { left: 238px; top: 118px; width: 714px; height: 419px; background: var(--card-dark); padding: 44px 44px 0; }
  .card-front { left: 231px; top: 645px; width: 711px; height: 415px; background: var(--card-light); }

  .help-title {
    font-family: "Roboto Condensed", sans-serif;
    font-weight: 700;
    font-size: 64px;
    line-height: 70px;
    color: var(--white);
    white-space: nowrap;
  }
  .help-rule {
    width: 120px; height: 6px;
    margin: 14px 0 26px;
    background: var(--gold);
  }
  .services { list-style: none; }
  .services li {
    font-family: "Montserrat", sans-serif;
    font-weight: 700;
    font-size: 22px;
    line-height: 46px;
    letter-spacing: 1px;
    color: var(--teal);
    white-space: nowrap;
  }
  .services .dot { color: var(--gold); padding: 0 8px; }

  .wave { position: absolute; inset: 0; width: 100%; height: 100%; }

  .holder-name {
    position: absolute; right: 34px; top: 38px;
    text-align: right;
    font-family: "Montserrat", sans-serif; font-weight: 700;
    font-size: 21px; line-height: 31px;
    color: var(--white);
  }

  .brand {
    position: absolute; left: 52px; top: 150px;
    display: flex; align-items: center; gap: 18px;
  }
  .brand-mark { width: 46px; height: 46px; background: var(--teal-deep); border-radius: 50%; }
  .brand-name {
    font-family: "Montserrat", sans-serif; font-weight: 700;
    font-size: 64px; letter-spacing: 4px;
    color: var(--teal-deep);
  }

  .contacts {
    position: absolute; left: 52px; top: 292px;
    list-style: none;
    font-family: "Roboto", sans-serif; font-size: 17.5px;
    color: var(--ink);
  }
  .contacts li { display: flex; align-items: center; height: 27px; }
  .contacts svg { width: 16px; height: 16px; margin-right: 18px; fill: var(--teal); }
</style>
</head>
<body>
<main class="canvas">

  <section class="card card-back">
    <h2 class="help-title">How can we help?</h2>
    <div class="help-rule"></div>
    <ul class="services">
      <li>MICROLEARNING<span class="dot">·</span>STORYBOARDS<span class="dot">·</span>LMS</li>
      <li>SCORM<span class="dot">·</span>xAPI<span class="dot">·</span>HTML5<span class="dot">·</span>VIDEO</li>
      <li>SIMULATIONS<span class="dot">·</span>ASSESSMENTS</li>
      <li>ACCESSIBILITY<span class="dot">·</span>LEARNER ANALYTICS</li>
    </ul>
  </section>

  <section class="card card-front">
    <svg class="wave" viewBox="0 0 711 415" preserveAspectRatio="none" aria-hidden="true">
      <defs>
        <linearGradient id="waveFill" x1="0" y1="0" x2="0" y2="1">
          <stop offset="0" stop-color="var(--teal-mint)"/>
          <stop offset="0.45" stop-color="var(--teal-deep)"/>
          <stop offset="1" stop-color="var(--teal-deep)"/>
        </linearGradient>
      </defs>
      <path d="M0,0 H711 V176 C600,170 520,130 440,92 C360,55 240,40 140,42 C80,43 30,50 0,58 Z" fill="url(#waveFill)"/>
      <path d="M0,48 C120,20 300,10 400,70" fill="none" stroke="var(--card-light)" stroke-width="9"/>
      <path d="M75,60 C230,45 360,60 460,110 C560,160 640,182 711,178" fill="none" stroke="var(--gold)" stroke-width="5"/>
    </svg>

    <div class="holder-name">Marta<br>Velder</div>

    <div class="brand">
      <span class="brand-mark"></span>
      <span class="brand-name">QVR</span>
    </div>

    <ul class="contacts">
      <li><svg viewBox="0 0 16 16"><path d="M3 2h3l1.5 3.5-2 1.2a8 8 0 0 0 3.8 3.8l1.2-2L14 10v3a1 1 0 0 1-1 1A12 12 0 0 1 2 3a1 1 0 0 1 1-1z"/></svg>646-555-0182</li>
      <li><svg viewBox="0 0 16 16"><circle cx="8" cy="8" r="6.5" fill="none" stroke="var(--teal)" stroke-width="1.6"/><path d="M1.5 8h13M8 1.5c-3 3.5-3 9.5 0 13M8 1.5c3 3.5 3 9.5 0 13" fill="none" stroke="var(--teal)" stroke-width="1.4"/></svg>www.quorvane.studio</li>
      <li><svg viewBox="0 0 16 16"><path d="M1 3h14v10H1z"/><path d="M1 3l7 6 7-6" fill="none" stroke="var(--card-light)" stroke-width="1.4"/></svg>mvelder@quorvane.studio</li>
    </ul>
  </section>

</main>
</body>
</html>
```